Building company needs a new logo and letterhead design

We need a new and refreshed logo and letterhead design for an existing building company. We specialise in residential as well as commercial building/construction, design and project management. Our company name is Vendaro Constructions Pty Ltd. Our primary colours that we want to use are black/orange/white. We do renovations/alterations/new homes both residential and commercial. We are a medium sized building company. We want something simple and modern.

Industry/Entity Type

Residential

```html
<!DOCTYPE html>
<html lang="en">
<head>
<meta charset="utf-8">
<title>Vendaro Constructions Pty Ltd — Letterhead</title>
<link rel="stylesheet" href="https://fonts.googleapis.com/css2?family=Crimson+Text:wght@400;700&display=swap">
<style>
  :root {
    --paper: #ffffff;
    --ink: #111111;
    --label: #5a2a0c;
    --orange: #f07a1a;
    --copper: #d9894f;
    --copper-soft: #f2c9a8;
  }
  html, body {
    margin: 0;
    padding: 0;
    overflow: hidden;
    background: var(--paper);
  }
  .letterhead {
    position: relative;
    width: 869px;
    height: 1200px;
    overflow: hidden;
    background: var(--paper);
    font-family: "Crimson Text", Georgia, serif;
    color: var(--ink);
  }
  .brand {
    position: absolute;
    left: 30px;
    top: 66px;
    display: flex;
    align-items: center;
    gap: 12px;
  }
  .brand-mark {
    width: 18px;
    height: 18px;
    background: var(--orange);
  }
  .brand-name {
    margin: 0;
    font-size: 30px;
    font-weight: 700;
    line-height: 1.05;
    color: var(--ink);
  }
  .brand-name span {
    display: block;
    font-size: 17px;
  }
  .contact {
    position: absolute;
    right: 43px;
    top: 38px;
    margin: 0;
    text-align: right;
    font-size: 19px;
    line-height: 24.6px;
  }
  .contact dt {
    display: inline;
    font-weight: 700;
    color: var(--label);
  }
  .contact dd {
    display: inline;
    margin: 0;
  }
  .contact dd::after {
    content: "";
    display: block;
  }
  .swirl {
    position: absolute;
    left: 360px;
    top: 830px;
    width: 509px;
    height: 370px;
    background:
      radial-gradient(ellipse 60% 45% at 72% 62%, var(--copper) 0%, rgba(217,137,79,0.55) 45%, rgba(242,201,168,0) 80%),
      radial-gradient(ellipse 80% 60% at 85% 80%, var(--copper-soft) 0%, rgba(255,255,255,0) 75%);
  }
</style>
</head>
<body>
  <main class="letterhead">
    <header>
      <div class="brand">
        <div class="brand-mark"></div>
        <h1 class="brand-name">Vendaro<span>Constructions Pty Ltd</span></h1>
      </div>
      <dl class="contact">
        <dt>Tel:</dt> <dd>0295550142</dd>
        <dt>Fax:</dt> <dd>0295550187</dd>
        <dt>Mobile:</dt> <dd>0400555318</dd>
        <dt>Email:</dt> <dd>office@vendarobuild.com</dd>
        <dt>Web:</dt> <dd>www.vendaroconstructions.com.au</dd>
        <dt>Address:</dt> <dd>PO Box 217, Lindfield Park, NSW&nbsp;&nbsp;2093</dd>
      </dl>
    </header>
    <div class="swirl" role="img" aria-label="Soft copper and orange abstract light-swirl decoration"></div>
  </main>
</body>
</html>
```